Corvins Pick 4 years in a row

I need a billboard that has all the attached logos and says:

Corvin's Pick Realtor 4 Years in a row!

1.75 Listing Fee

Marcus Olvery

410-555-0182

and somewhere very small at the bottom:

833-555-0147

2847 W Pennick Rd, Bel Air, MD 21014

I put in the last winner just to give an idea of what I'm looking for, although I'd like to switch it up a little bit.

```html
<!DOCTYPE html>
<html lang="en">
<head>
<meta charset="utf-8">
<title>Marcus Olvery – Billboard</title>
<link rel="stylesheet" href="https://fonts.googleapis.com/css2?family=Lexend:wght@400;500;600;700;800&family=Cinzel:wght@500&display=swap">
<style>
  :root {
    --navy: #151a2c;
    --panel-light: #f4f4f5;
    --panel-mid: #d9dadd;
    --ink: #171b2b;
    --white: #ffffff;
    --badge-orange: #e07a2a;
    --stage: #e9ebee;
    --laurel: #6f7d6f;
  }
  * { margin: 0; padding: 0; box-sizing: border-box; }
  html, body { width: 1200px; height: 900px; overflow: hidden; }
  body {
    background: var(--stage);
    font-family: "Lexend", sans-serif;
    color: var(--ink);
    position: relative;
  }
  .billboard {
    position: absolute;
    left: 30px; top: 280px;
    width: 1140px; height: 340px;
    background: radial-gradient(ellipse at 45% 40%, var(--panel-light) 0%, #eaeaec 45%, var(--panel-mid) 100%);
    overflow: hidden;
  }
  .agent-photo {
    position: absolute;
    left: 30px; top: 30px;
    width: 300px; height: 280px;
    background: linear-gradient(180deg, #e6e6e8 0%, #2b3556 55%, #1e2640 100%);
  }
  .agent-name {
    position: absolute;
    left: 345px; top: 38px;
    font-weight: 800;
    font-size: 70px;
    line-height: 0.88;
    letter-spacing: 1px;
    text-transform: uppercase;
  }
  .name-rule {
    position: absolute;
    left: 345px; top: 176px;
    width: 320px; height: 2px;
    background: var(--ink);
  }
  .tagline {
    position: absolute;
    left: 345px; top: 186px;
    font-size: 15px;
    font-weight: 600;
  }
  .contact-band {
    position: absolute;
    left: 335px; top: 222px;
    width: 805px; height: 74px;
    background: var(--navy);
    color: var(--white);
    display: flex;
    align-items: center;
    padding-left: 12px;
    white-space: nowrap;
  }
  .contact-label { font-size: 32px; font-weight: 500; margin-right: 18px; }
  .contact-phone { font-size: 64px; font-weight: 800; letter-spacing: 3px; }
  .footer-line {
    position: absolute;
    left: 345px; top: 306px;
    font-size: 14px;
    font-weight: 600;
    letter-spacing: 0.5px;
    white-space: nowrap;
  }
  .feature-box {
    position: absolute;
    top: 62px;
    width: 150px; height: 175px;
    background: var(--navy);
    border-radius: 16px;
    color: var(--white);
    text-align: center;
    text-transform: uppercase;
    font-weight: 700;
  }
  .feature-box--award { left: 690px; }
  .feature-box--fee { left: 855px; display: flex; align-items: center; justify-content: center; font-size: 27px; line-height: 1.05; }
  .award-seal {
    display: block;
    margin: 16px auto 10px;
    width: 62px; height: 62px;
    border-radius: 50%;
    background: #242a3f;
    border: 3px solid var(--badge-orange);
  }
  .award-title { font-size: 24px; line-height: 1; }
  .award-sub { font-size: 14px; font-weight: 500; margin-top: 2px; }
  .team-mark {
    position: absolute;
    left: 1018px; top: 112px;
    width: 110px;
    text-align: center;
    color: var(--ink);
  }
  .team-dot {
    display: block;
    margin: 0 auto 8px;
    width: 40px; height: 40px;
    border-radius: 50%;
    background: var(--laurel);
  }
  .team-name { font-size: 15px; font-weight: 500; line-height: 1.15; text-transform: uppercase; }
</style>
</head>
<body>
  <section class="billboard">
    <div class="agent-photo" role="img" aria-label="Portrait photo of the realtor in a navy suit"></div>

    <h1 class="agent-name">Marcus<br>Olvery</h1>
    <div class="name-rule"></div>
    <p class="tagline">Corvin's Pick Realtor 4 Years in a row!</p>

    <div class="feature-box feature-box--award">
      <span class="award-seal" aria-hidden="true"></span>
      <div class="award-title">Real<br>Estate</div>
      <div class="award-sub">Professional</div>
    </div>

    <div class="feature-box feature-box--fee">1.75%<br>Fee<br>Listing<br>Service</div>

    <div class="team-mark">
      <span class="team-dot" aria-hidden="true"></span>
      <div class="team-name">The Summit Team</div>
    </div>

    <div class="contact-band">
      <span class="contact-label">CALL/TEXT:</span>
      <span class="contact-phone">410-555-0182</span>
    </div>

    <p class="footer-line">2847 W Pennick Rd, Bel Air, MD 21014 | 833-555-0147 | www.summitteamsells.com</p>
  </section>
</body>
</html>
```